Chilli Sauce - Label for Chilli Sauce bottle

I want a design for my chilli sauce label. I have included an example from an existing product. The key features of a successful design are as follows:
1. It shows the supplier: Bramble Ridge Condiments or Bramble Ridge if a shorter label fits better.
2. We need to have space for the ingredients. We will add these after.
3. Simple is good, refer attached. It doesn't need to be a design/logo, but a great design would be wonderful.
4. Some ideas. Bramble Ridge at the top of the label. Chilli Sauce in the middle of the label. Made with local ingredients (optional). Contains chilli - believe it or not (optional or similar wording)

```html
<!DOCTYPE html>
<html lang="en">
<head>
<meta charset="utf-8">
<title>Bramble Ridge Chilli Sauce Label</title>
<link href="https://fonts.googleapis.com/css2?family=Bebas+Neue&family=Kaushan+Script&family=Oswald:wght@300;400;500&family=Roboto+Condensed:wght@400;700&display=swap" rel="stylesheet">
<style>
  :root {
    --label-red: #d71f26;
    --ink-navy: #1b2337;
    --sun-yellow: #f8c012;
    --paper: #ffffff;
  }
  * { margin: 0; padding: 0; box-sizing: border-box; }
  html, body { width: 900px; height: 1200px; overflow: hidden; background: var(--paper); }
  .canvas { position: relative; width: 900px; height: 1200px; background: var(--paper); }

  .label {
    position: absolute; left: 20px; top: 404px;
    width: 860px; height: 391px;
    background: var(--label-red);
    color: var(--paper);
  }

  /* Nutrition panel */
  .nutrition {
    position: absolute; left: 42px; top: 41px; width: 158px; height: 240px;
    background: var(--paper); color: #000;
    border: 1px solid #000; outline: 1px solid var(--paper);
    padding: 3px 3px;
    font-family: Arial, Helvetica, sans-serif;
    font-size: 6.2px; line-height: 1.25;
  }
  .nutrition__title { font-weight: 900; font-size: 17px; letter-spacing: 0.6px; line-height: 1; border-bottom: 1px solid #000; padding-bottom: 2px; }
  .nutrition__servings { font-size: 8px; padding-top: 2px; }
  .nutrition__size { display: flex; justify-content: space-between; font-weight: 700; font-size: 8px; border-bottom: 5px solid #000; padding-bottom: 1px; }
  .nutrition__amount { font-weight: 700; font-size: 6px; padding-top: 2px; }
  .nutrition__calories { display: flex; justify-content: space-between; align-items: flex-end; font-weight: 900; font-size: 13px; line-height: 1; border-bottom: 3px solid #000; padding-bottom: 1px; }
  .nutrition__calories span:last-child { font-size: 18px; }
  .nutrition__dv { text-align: right; font-weight: 700; font-size: 5px; border-bottom: 1px solid #000; padding: 1px 0; }
  .nutrition__row { display: flex; justify-content: space-between; border-bottom: 0.5px solid #000; padding: 0.9px 0; }
  .nutrition__row b { font-weight: 700; }
  .nutrition__row--indent { padding-left: 9px; }
  .nutrition__row--indent2 { padding-left: 19px; }
  .nutrition__row--last { border-bottom: 4px solid #000; }
  .nutrition__note { font-size: 4.6px; line-height: 1.2; padding-top: 2px; }
  .nutrition__note + .nutrition__note { border-top: 0.5px solid #000; margin-top: 3px; }

  .origin {
    position: absolute; left: 42px; top: 310px; width: 158px;
    text-align: center; font-family: "Roboto Condensed", sans-serif;
    font-size: 9.5px; line-height: 1.2; letter-spacing: 0.2px;
  }
  .origin strong { font-weight: 700; }

  /* Centre brand block */
  .brand { position: absolute; left: 282px; top: 44px; width: 300px; text-align: center; }
  .brand__name { font-family: "Bebas Neue", sans-serif; font-weight: 400; font-size: 42px; line-height: 0.9; letter-spacing: 0.5px; }
  .brand__sub { font-family: "Kaushan Script", cursive; color: var(--sun-yellow); font-size: 24px; line-height: 1; margin-top: -2px; }

  .product-title {
    position: absolute; left: 326px; top: 122px; width: 218px; height: 134px;
    background: var(--ink-navy); border-radius: 14px 30px 18px 34px;
    transform: rotate(-3deg);
    font-family: "Kaushan Script", cursive; color: var(--sun-yellow);
    font-size: 56px; line-height: 0.95; font-weight: 400;
    padding: 8px 10px 0 12px;
  }
  .product-title span { display: block; }
  .product-title__second { padding-left: 48px; }

  .tagline {
    position: absolute; left: 282px; top: 266px; width: 300px; text-align: center;
    font-family: "Kaushan Script", cursive; color: var(--ink-navy);
    font-size: 23px; line-height: 1.15;
  }
  .volume {
    position: absolute; left: 282px; top: 326px; width: 300px; text-align: center;
    font-family: "Bebas Neue", sans-serif; font-size: 27px; letter-spacing: 0.5px;
  }

  /* Right column */
  .ingredients {
    position: absolute; left: 647px; top: 47px; width: 152px; text-align: center;
    font-family: "Oswald", sans-serif; font-weight: 300;
    font-size: 9px; line-height: 12.5px; text-transform: uppercase;
  }
  .heat__label { position: absolute; left: 641px; top: 215px; font-family: "Bebas Neue", sans-serif; font-size: 16px; line-height: 1; }
  .heat__chilli { position: absolute; left: 632px; top: 180px; width: 70px; height: 140px; }
  .heat__badge {
    position: absolute; left: 690px; top: 229px; width: 94px; height: 90px;
    background: var(--ink-navy); border-radius: 10px;
    display: flex; flex-direction: column; justify-content: center; align-items: center;
    font-family: "Kaushan Script", cursive; color: var(--sun-yellow);
    font-size: 24px; line-height: 0.95;
  }
  .care {
    position: absolute; left: 640px; top: 337px; width: 172px; text-align: center;
    font-family: "Roboto Condensed", sans-serif; font-weight: 700; font-size: 10px; letter-spacing: 0.2px;
  }
</style>
</head>
<body>
<main class="canvas">
  <section class="label">

    <div class="nutrition">
      <div class="nutrition__title">Nutrition Facts</div>
      <div class="nutrition__servings">24 servings per container</div>
      <div class="nutrition__size"><span>Serving size</span><span>1 tsp (5ml)</span></div>
      <div class="nutrition__amount">Amount Per Serving</div>
      <div class="nutrition__calories"><span>Calories</span><span>0</span></div>
      <div class="nutrition__dv">% Daily Value*</div>
      <div class="nutrition__row"><span><b>Total Fat</b> 0g</span><b>0%</b></div>
      <div class="nutrition__row nutrition__row--indent"><span>Saturated Fat 0g</span><b>0%</b></div>
      <div class="nutrition__row nutrition__row--indent"><span><i>Trans</i> Fat 0g</span><span></span></div>
      <div class="nutrition__row"><span><b>Cholesterol</b> 0mg</span><b>0%</b></div>
      <div class="nutrition__row"><span><b>Sodium</b> 90mg</span><b>4%</b></div>
      <div class="nutrition__row"><span><b>Total Carbohydrate</b> 0g</span><b>0%</b></div>
      <div class="nutrition__row nutrition__row--indent"><span>Dietary Fiber 0g</span><b>0%</b></div>
      <div class="nutrition__row nutrition__row--indent"><span>Total Sugars 0g</span><span></span></div>
      <div class="nutrition__row nutrition__row--indent2"><span>Includes 0g Added Sugars</span><b>0%</b></div>
      <div class="nutrition__row nutrition__row--last"><span><b>Protein</b> 0g</span><b>0%</b></div>
      <div class="nutrition__note">Not a significant source of vitamin D, calcium, iron, and potassium</div>
      <div class="nutrition__note">*The % Daily Value (DV) tells you how much a nutrient in a serving of food contributes to a daily diet. 2,000 calories a day is used for general nutrition advice.</div>
    </div>

    <p class="origin"><strong>PRODUCT OF AUSTRALIA</strong><br>DISTRIBUTED BY<br>BRAMBLE RIDGE CONDIMENTS</p>

    <header class="brand">
      <h1 class="brand__name">BRAMBLE RIDGE</h1>
      <p class="brand__sub">Condiments</p>
    </header>

    <h2 class="product-title"><span>Chilli</span><span class="product-title__second">Sauce</span></h2>

    <p class="tagline">With Australian<br>Grown Chillies</p>
    <p class="volume">150 ML / 5.07 OZ</p>

    <p class="ingredients">Ingredients: water, chilli peppers, tomato, salt, spices, pH control agent (acetic acid), stabilizer (xanthan gum), acidifier (citric acid), sodium benzoate as a preservtive and FD&amp;C Red 40.</p>

    <span class="heat__label">HOT</span>
    <svg class="heat__chilli" viewBox="0 0 70 140" role="img" aria-label="Chilli heat meter illustration graded from red to green">
      <defs>
        <linearGradient id="heatTone" x1="0" y1="0" x2="0" y2="1">
          <stop offset="0" stop-color="#1b2337"/>
          <stop offset="0.3" stop-color="#f15a24"/>
          <stop offset="0.7" stop-color="#f8c012"/>
          <stop offset="1" stop-color="#6cbf3a"/>
        </linearGradient>
      </defs>
      <rect x="36" y="0" width="22" height="140" rx="10" fill="url(#heatTone)"/>
    </svg>
    <div class="heat__badge"><span>Extra</span><span>Spice</span></div>

    <p class="care">KEEP IN A FRESH AND DRY PLACE</p>
  </section>
</main>
</body>
</html>
```